Business card por a urban DJ, up scale audience target

Need a sober design, modern, conservative colors but i can consider some options, y play rnb, hip hop, EDM and top40.

Business card for contact and personal info, double sided, use logo attrached please; im 42 so i need a card acording to my age an target audience.

Target Market(s)

Adult people, up scale audience

Industry/Entity Type

Music Download

Contact Information for Business Card

Cel (318) 4207265518 www.lumadrift.com

Requirements
Must have
• open mind
Nice to have
• open mind
Should not have
• DJ

```html
<!DOCTYPE html>
<html lang="en">
<head>
<meta charset="utf-8">
<title>Luma – Business Card</title>
<link rel="stylesheet" href="https://fonts.googleapis.com/css2?family=Exo+2:wght@500;600&display=swap">
<style>
  :root {
    --bg: #2b2e30;
    --card-black: #141516;
    --silver: #d9dadb;
    --text-light: #f1f1f1;
    --photo-dark: #1a1a1a;
    --photo-mid: #5a5a5a;
    --photo-light: #c9c9c9;
  }
  * { margin: 0; padding: 0; box-sizing: border-box; }
  html, body {
    width: 1200px;
    height: 675px;
    overflow: hidden;
    background: var(--bg);
    font-family: "Exo 2", sans-serif;
  }
  .stage {
    width: 1200px;
    height: 675px;
    display: flex;
    align-items: center;
    justify-content: center;
    gap: 60px;
  }
  .card {
    width: 490px;
    height: 280px;
    position: relative;
    overflow: hidden;
    box-shadow: 0 14px 30px rgba(0,0,0,0.35);
  }
  .card-front {
    background: var(--card-black);
    display: flex;
    align-items: center;
    justify-content: center;
  }
  .brand-name {
    font-weight: 600;
    letter-spacing: 0.06em;
    line-height: 1;
  }
  .card-front .brand-name {
    font-size: 64px;
    color: var(--silver);
  }
  .card-back { background: var(--photo-dark); }
  .crowd-photo {
    position: absolute;
    inset: 0;
    background:
      radial-gradient(ellipse 60% 45% at 55% 10%, var(--photo-light) 0%, rgba(150,150,150,0.6) 40%, transparent 75%),
      linear-gradient(180deg, var(--photo-mid) 0%, #3a3a3a 45%, var(--photo-dark) 100%);
  }
  .back-content {
    position: relative;
    height: 100%;
    display: flex;
    flex-direction: column;
    align-items: center;
    padding-top: 46px;
  }
  .back-content .brand-name {
    font-size: 56px;
    color: var(--card-black);
  }
  .brand-rule {
    width: 150px;
    height: 2px;
    background: var(--card-black);
    margin-top: 8px;
  }
  .genres {
    margin-top: 8px;
    font-size: 13px;
    font-weight: 500;
    letter-spacing: 0.18em;
    color: var(--card-black);
    word-spacing: 0.6em;
  }
  .contact {
    list-style: none;
    margin-top: 34px;
    color: var(--text-light);
    font-size: 17px;
    font-weight: 500;
    letter-spacing: 0.05em;
  }
  .contact li {
    display: flex;
    align-items: center;
    gap: 10px;
    margin-bottom: 10px;
  }
  .contact svg { width: 14px; height: 14px; flex: none; }
</style>
</head>
<body>
  <main class="stage">
    <section class="card card-front" aria-label="Card front">
      <span class="brand-name">LUMA</span>
    </section>

    <section class="card card-back" aria-label="Card back">
      <div class="crowd-photo" role="img" aria-label="Black and white concert crowd with raised hands under stage lights"></div>
      <div class="back-content">
        <span class="brand-name">LUMA</span>
        <div class="brand-rule"></div>
        <p class="genres">RNB HIPHOP EDM</p>
        <ul class="contact">
          <li>
            <svg viewBox="0 0 14 14" aria-hidden="true"><rect x="3.5" y="0.8" width="7" height="12.4" rx="1.2" fill="none" stroke="currentColor" stroke-width="1.2"/><line x1="6" y1="11" x2="8" y2="11" stroke="currentColor" stroke-width="1"/></svg>
            <span>(318) 4207265518</span>
          </li>
          <li>
            <svg viewBox="0 0 14 14" aria-hidden="true"><circle cx="7" cy="7" r="6" fill="none" stroke="currentColor" stroke-width="1.2"/><ellipse cx="7" cy="7" rx="2.6" ry="6" fill="none" stroke="currentColor" stroke-width="1"/><line x1="1" y1="7" x2="13" y2="7" stroke="currentColor" stroke-width="1"/></svg>
            <span>www.lumadrift.com</span>
          </li>
        </ul>
      </div>
    </section>
  </main>
</body>
</html>
```